Orthobiologic, StemCell, Bone Marrow Aspirate Device Distributor

We need a wordpress fully functioning website design for an innovative ortho-biologic, Bone Marrow Aspirate Device that extracts stem cells for orthopedic regenerative medical professionals. We also offer state of the art training in there office setting with licensed medical staff, a full service support team, and software for tracking patient outcome over time. We are an innovative company that prides itself on gold standard support. We will have other offerings on our website and would like a spot for "future" products. We would like to see designs that look professional, medical, and convey support, security, science, and innovation. We prefer shades of blue and red/orange. I particularly like the following websites that also sell the same device in order of preference:regenacelltherapy.comhttps://aspire-medical.eu/marrow-cellution/https://www.matrixbiosurgical.com/#emerging-solutions-in-healthcareElite2elite.comI have attached a few pictures of the device for reference

Target Market(s)

Orthopedics, Regenerative medicine doctors, Industry representatives, Hospitals

Industry/Entity Type

Medical Equipment

Coding

Coded - Design and coding required

Colors
3176b5
33a6d7
f37022
ec1f27

Requirements
Must have
• It must be able to have videos which I can supply, email, online ordering, and sfax. I have a domain name Coralweavesolutions.com . It must have a FAQ section which you can obtain some information from https://www.tolvenclinical.com/solutions#resources
• The device is manufactured by Dulmor and this is the link to the product page http://www.dulmor.com/quintadraw
• I am currently working on a custom logo and should be able to supply that in short order. I prefer shades of blue and red.
Nice to have
• I would love to have a graphic video as seen here: please see quinta draw vs bone marrow aspirate concentrate.
• https://www.tolvenclinical.com/solutions#competition
• I would pay considerably more to have something similar if it is at all possible
Should not have
• Nothing specific

```html
<!DOCTYPE html>
<html lang="en">
<head>
<meta charset="utf-8">
<title>Coral Weave Solutions</title>
<link href="https://fonts.googleapis.com/css2?family=Lato:wght@300;400;700&display=swap" rel="stylesheet">
<style>
:root{
  --blue:#3176b5;
  --blue-deep:#1f5fae;
  --sky:#33a6d7;
  --orange:#f37022;
  --red:#ec1f27;
  --ink:#333;
  --muted:#666;
  --light:#f2f2f2;
  --white:#fff;
}
*{box-sizing:border-box;margin:0;padding:0}
html,body{width:1200px;height:4505px;overflow:hidden}
body{position:relative;font-family:'Lato',sans-serif;color:var(--ink);background:var(--white)}
section,header,footer{position:absolute;left:0;width:1200px}
.abs{position:absolute}
.center{left:0;width:1200px;text-align:center}
.btn{position:absolute;display:flex;align-items:center;justify-content:center;border:2px solid var(--white);border-radius:30px;color:var(--white);font-size:15px;font-weight:700;letter-spacing:.3px}
.btn-red{border:2px solid var(--red);color:var(--red);font-size:12px;font-weight:400}

/* header */
.site-header{top:0;height:95px;background:var(--white);border-bottom:1px solid #e4e4e4}
.brand{left:149px;top:18px;color:var(--blue);font-weight:700;line-height:1}
.brand .line1{font-size:27px;letter-spacing:.5px}
.brand .line2{font-size:20px;letter-spacing:5px;margin-top:4px}
.nav{left:412px;top:38px;display:flex;gap:37px;font-size:18px;color:#222}

/* hero */
.hero{top:95px;height:570px;background:linear-gradient(120deg,#1a56b8 0%,#1f6bd0 45%,#2b9ad8 75%,#1c5fc0 100%)}
.hero-title{top:215px;font-size:48px;color:var(--white);font-weight:400;letter-spacing:1px}
.hero-sub{top:279px;font-size:24px;color:var(--white);font-weight:400}
.slide-arrow{top:230px;width:56px;height:56px;border-radius:50%;background:rgba(255,255,255,.45)}

/* about */
.about{top:665px;height:378px}
.about h2{top:85px;font-size:34px;font-weight:400;color:var(--blue)}
.about p{top:147px;left:260px;width:680px;text-align:center;font-size:17px;line-height:27px;color:var(--muted);font-weight:400}

/* who */
.who{top:1043px;height:456px;background:linear-gradient(100deg,#2a6fbf 0%,#2f86d0 45%,#2968b8 100%)}
.who-art{left:0;top:0;width:560px;height:456px;background:radial-gradient(ellipse at 50% 45%,rgba(20,50,120,.55),rgba(40,110,200,0) 65%)}
.who h2{left:610px;top:112px;font-size:31px;color:var(--white);font-weight:400}
.who p{left:610px;top:174px;width:450px;font-size:15px;line-height:21px;color:var(--white)}

/* offer / why */
.offer{top:1499px;height:540px}
.offer-left{left:0;top:0;width:606px;height:540px;background:linear-gradient(140deg,var(--orange) 0%,#ea4a1f 50%,var(--red) 100%)}
.offer-left h2{left:169px;top:88px;font-size:31px;color:var(--white);font-weight:400}
.offer-left p{left:171px;width:385px;font-size:15px;line-height:27px;color:var(--white)}
.why h2{left:647px;top:83px;font-size:31px;color:var(--blue);font-weight:400}
.why-item{left:650px;width:470px}
.why-item svg{position:absolute;left:0;top:0}
.why-item h3{position:absolute;left:86px;top:0;font-size:18px;font-weight:700;color:#222}
.why-item p{position:absolute;left:87px;top:29px;width:360px;font-size:13.5px;line-height:21px;color:var(--muted)}

/* mission */
.mission{top:2039px;height:525px;background:linear-gradient(90deg,#111 0%,#3a3a3a 30%,#2a2a2a 70%,#0e0e0e 100%)}
.mission-box{left:264px;top:77px;width:666px;height:364px;background:rgba(40,120,200,.88)}
.mission-box h2{top:69px;left:0;width:666px;text-align:center;font-size:33px;color:var(--white);font-weight:400}
.mission-box p{top:126px;left:60px;width:546px;text-align:center;font-size:17px;line-height:27px;color:var(--white)}

/* products */
.products{top:2564px;height:591px}
.products h2{top:75px;font-size:32px;font-weight:400;color:#222}
.card{top:149px;width:279px;height:361px;border:2px solid #e2e2e2;background:var(--white)}
.card .shot{position:absolute;left:30px;top:22px;width:215px;height:160px;border-radius:4px}
.card h3{position:absolute;left:0;top:207px;width:275px;text-align:center;font-size:17px;font-weight:700;color:#222}
.card p{position:absolute;left:25px;top:238px;width:225px;text-align:center;font-size:12.5px;line-height:21px;color:var(--muted)}
.card .btn-red{left:67px;top:286px;width:140px;height:42px}

/* faq */
.faq{top:3155px;height:581px;background:linear-gradient(135deg,var(--orange) 0%,#ee4222 55%,var(--red) 100%)}
.faq h2{top:50px;font-size:33px;color:var(--white);font-weight:400}
.faq-item{left:222px;width:764px;border:2px solid rgba(255,255,255,.8);color:var(--white)}
.faq-item h3{position:absolute;left:22px;font-size:13.5px;font-weight:700;line-height:21px;width:640px}
.faq-item p{position:absolute;left:22px;top:70px;width:700px;font-size:13px;line-height:19px}
.faq-item .sign{position:absolute;right:20px;font-size:24px;font-weight:400}

/* tiles */
.tiles{top:3736px;height:374px}
.tile{top:0;height:374px}
.tile h2{position:absolute;left:0;width:100%;text-align:center;top:130px;font-size:28px;color:var(--white);font-weight:400}
.tile .btn{top:200px;height:42px;width:140px;font-size:12px;font-weight:400}

/* footer */
.site-footer{top:4110px;height:326px;background:var(--light)}
.foot-col{top:82px}
.foot-col h4{font-size:15px;font-weight:700;color:#222;margin-bottom:15px}
.foot-col li{list-style:none;font-size:13.5px;color:#555;line-height:26px}
.contact-line{display:flex;gap:12px;font-size:13.5px;color:#555;line-height:17px;margin-bottom:18px}
.social li{display:flex;align-items:center;gap:12px;line-height:34px}
.social .dot{width:20px;height:20px;border-radius:50%;background:var(--blue)}
.copyright{top:4436px;height:69px;background:var(--light);border-top:1px solid #ddd;display:flex;align-items:center;justify-content:center;font-size:13px;color:#999}
</style>
</head>
<body>

<header class="site-header">
  <div class="abs brand"><div class="line1">CORAL WEAVE</div><div class="line2">SOLUTIONS</div></div>
  <nav class="abs nav"><span>ABOUT</span><span>PRODUCTS</span><span>SERVICES</span><span>SOLUTION</span><span>NEWS</span><span>CONTACT</span></nav>
</header>

<section class="hero" role="img" aria-label="Blue-tinted photograph of a seated person with the knee and leg skeleton highlighted">
  <div class="abs slide-arrow" style="left:107px"><svg width="56" height="56" viewBox="0 0 56 56"><path d="M32 18 L22 28 L32 38" fill="none" stroke="#1d3f7a" stroke-width="3"/></svg></div>
  <div class="abs slide-arrow" style="left:1065px"><svg width="56" height="56" viewBox="0 0 56 56"><path d="M24 18 L34 28 L24 38" fill="none" stroke="#1d3f7a" stroke-width="3"/></svg></div>
  <h1 class="abs center hero-title">INNOVATIVE ORTHO-BIOLOGIC</h1>
  <p class="abs center hero-sub">EXTRACTS STEM CELLS FOR ORTHOPEDIC REGENERATIVE</p>
</section>

<section class="about">
  <h2 class="abs center">ABOUT CORAL WEAVE SOLUTIONS</h2>
  <p class="abs">Coral Weave Solutions is a provider of quality, innovative regenerative medicine and ortho-biologic devices coupled with best in class clinical training. We have diverse experience in regenerative solutions as well as exceptional clinical expertise.</p>
  <svg class="abs" style="left:582px;top:272px" width="36" height="46" viewBox="0 0 36 46"><path d="M18 2 V42 M4 28 L18 42 L32 28" fill="none" stroke="var(--blue)" stroke-width="2.5"/></svg>
</section>

<section class="who">
  <div class="abs who-art" role="img" aria-label="Blue X-ray image of the pelvis and lower spine"></div>
  <h2 class="abs">WHO WE ARE</h2>
  <p class="abs">Providers of Innovative Ortho Biologic devices staffed with clinical professionals who bring exciting new biologic options to busy practitioners, hospitals, and surgical centers.</p>
  <div class="btn" style="left:610px;top:265px;width:163px;height:51px">CLICK HERE</div>
</section>

<section class="offer">
  <div class="abs offer-left">
    <h2 class="abs">WHAT WE OFFER</h2>
    <p class="abs" style="top:145px">Gold standard client support with effective and efficient treatment solutions for physicians and their patients as well as on-site, personalized, hands-on training with our licensed clinical specialists.</p>
    <p class="abs" style="top:280px">Our expertise in the clinical use of these technologies and our ability to give hands on training sets the gold standard in our industry. We are driven by a commitment to improve patient outcomes, reduce provider expenses with cost effective products</p>
  </div>
  <div class="why">
    <h2 class="abs">WHY WE ARE</h2>
    <div class="abs why-item" style="top:152px">
      <svg width="64" height="70" viewBox="0 0 64 70" fill="none" stroke="var(--orange)" stroke-width="2"><path d="M32 6 C18 6 10 16 12 28 C13 36 20 40 22 46 V54 H42 V46 C44 40 51 36 52 28 C54 16 46 6 32 6 Z"/><path d="M24 60 H40 M27 66 H37 M32 14 V46 M22 24 H42 M24 34 H40"/><circle cx="6" cy="20" r="2"/><circle cx="58" cy="20" r="2"/></svg>
      <h3>INNOVATIVE</h3>
      <p>Vivamus porttitor purus nisi eleifend libero a tempus libero lectus feugiat felis Morbi diam mauris viverra in</p>
    </div>
    <div class="abs why-item" style="top:271px">
      <svg width="64" height="64" viewBox="0 0 64 64" fill="none" stroke="var(--orange)" stroke-width="2"><circle cx="32" cy="32" r="28"/><circle cx="32" cy="32" r="20"/><path d="M32 32 L44 20 M18 38 H46"/><circle cx="32" cy="32" r="3"/></svg>
      <h3>EFFICIENT</h3>
      <p>Vivamus porttitor purus nisi eleifend libero a tempus libero lectus feugiat felis Morbi diam mauris</p>
    </div>
    <div class="abs why-item" style="top:389px">
      <svg width="64" height="70" viewBox="0 0 64 70" fill="none" stroke="var(--orange)" stroke-width="2"><path d="M32 4 C16 4 6 16 6 30 C6 44 18 54 30 54 L20 66 L42 52 C52 46 58 38 58 30 C58 16 48 4 32 4 Z"/><circle cx="32" cy="28" r="8"/></svg>
      <h3>SPECIFIC</h3>
      <p>Vivamus porttitor purus nisi eleifend libero a tempus libero lectus feugiat felis Morbi diam mauris</p>
    </div>
  </div>
</section>

<section class="mission" role="img" aria-label="Black and white X-ray of hip and knee joints">
  <div class="abs mission-box">
    <h2 class="abs">OUR MISSION</h2>
    <p class="abs">To provide medical professionals with the training and tools they need to offer regenerative medical therapies that will become the gold standard of care for the treatment of multiple ortho degenerative diseases and ortho biologic conditions.</p>
    <div class="btn" style="left:252px;top:254px;width:163px;height:48px">CLICK HERE</div>
  </div>
</section>

<section class="products">
  <h2 class="abs center">OUR PRODUCTS</h2>
  <div class="abs card" style="left:160px">
    <div class="shot" role="img" aria-label="Purple aspiration needle with a T-handle" style="background:linear-gradient(135deg,#fff 20%,#d8cdef 50%,#fff 80%)"></div>
    <h3>PRODUCT TITLE</h3>
    <p>Sed ut perspiciatis unde omnis iste natus error sit voluptatem</p>
    <div class="btn btn-red">CLICK HERE</div>
  </div>
  <div class="abs card" style="left:456px">
    <div class="shot" role="img" aria-label="Blue aspiration device with plunger and spring" style="background:linear-gradient(135deg,#fff 20%,#cfd3f2 50%,#fff 80%)"></div>
    <h3>PRODUCT TITLE</h3>
    <p>Sed ut perspiciatis unde omnis iste natus error sit voluptatem</p>
    <div class="btn btn-red">CLICK HERE</div>
  </div>
  <div class="abs card" style="left:752px">
    <div class="shot" role="img" aria-label="Stainless steel cannula tip with side ports" style="background:linear-gradient(135deg,#fff 20%,#dedede 50%,#fff 80%)"></div>
    <h3>PRODUCT TITLE</h3>
    <p>Sed ut perspiciatis unde omnis iste natus error sit voluptatem</p>
    <div class="btn btn-red">CLICK HERE</div>
  </div>
</section>

<section class="faq">
  <h2 class="abs center">FAQ</h2>
  <div class="abs faq-item" style="top:112px;height:131px">
    <h3 style="top:14px">DOES A SMALL VOLUME ASPIRATE HAVE MORE CFU-F THAN A LARGER DRAW THAT IS THEN VOLUME REDUCED BY CENTRIFUGATION?</h3>
    <span class="sign" style="top:12px">–</span>
    <p>Pellentesque faucibus Ut accumsan ultricies elit Maecenas at justo id velit placerat molestie Donec dictum lectus non odio Cras a ante vitae enim iaculis aliquam Mauris nunc quam venenatis nec</p>
  </div>
  <div class="abs faq-item" style="top:259px;height:75px">
    <h3 style="top:14px">WHAT ARE THE LIMITATIONS OF TRADITIONAL NEEDLES AND WHAT IS THE OPTIMAL TECHNIQUE FOR MINIMIZAING PERIPHERAL BLOOD DILUTION?</h3>
    <span class="sign" style="top:20px">+</span>
  </div>
  <div class="abs faq-item" style="top:345px;height:75px">
    <h3 style="top:14px">DO I NEED TO FILTER SPICULES FROM MARROW AFTER ASPIRATION AND ARE RED CELLS A PROBLEM?</h3>
    <span class="sign" style="top:20px">+</span>
  </div>
  <div class="abs faq-item" style="top:427px;height:75px">
    <h3 style="top:14px">IS THERE A RELATIONSHIP BETWEEN DIFFERING VOLUMES OF BONE MARROW ASPIRATES AND THEIR CELLULAR COMPOSITION?</h3>
    <span class="sign" style="top:20px">+</span>
  </div>
</section>

<section class="tiles">
  <div class="abs tile" style="left:0;width:397px;background:linear-gradient(180deg,#0f2a55,#16386e)" role="img" aria-label="Dark blue X-ray of a torso and spine">
    <h2>DISTRIBUTORS</h2>
    <div class="btn" style="left:125px">CLICK HERE</div>
  </div>
  <div class="abs tile" style="left:397px;width:404px;background:linear-gradient(160deg,#2c6fd0,#1d4fae)" role="img" aria-label="Blue-tinted photo of an X-ray film being examined">
    <h2>FAQ</h2>
    <div class="btn" style="left:135px">CLICK HERE</div>
  </div>
  <div class="abs tile" style="left:801px;width:399px;background:linear-gradient(180deg,#0e2a5a,#163c7a)" role="img" aria-label="Dark blue X-ray of the pelvis and hip joints">
    <h2>RESOURCES</h2>
    <div class="btn" style="left:134px">CLICK HERE</div>
  </div>
</section>

<footer class="site-footer">
  <div class="abs foot-col" style="left:170px">
    <h4>CONTACT US</h4>
    <div class="contact-line"><svg width="16" height="20" viewBox="0 0 16 20"><path d="M8 1 C4 1 1.5 4 1.5 7.5 C1.5 12 8 19 8 19 C8 19 14.5 12 14.5 7.5 C14.5 4 12 1 8 1 Z" fill="none" stroke="#333" stroke-width="1.6"/><circle cx="8" cy="7.5" r="2.3" fill="none" stroke="#333" stroke-width="1.6"/></svg><span>245 Linden Avenue #4B<br>Texas 75201 TX</span></div>
    <div class="contact-line"><svg width="16" height="16" viewBox="0 0 16 16"><path d="M3 1.5 L6 4.5 L4.5 6.5 C5.5 8.5 7.5 10.5 9.5 11.5 L11.5 10 L14.5 13 L12.5 15 C7 14 2 9 1 3.5 Z" fill="none" stroke="#333" stroke-width="1.4"/></svg><span>555.014.2290</span></div>
    <div class="contact-line"><svg width="16" height="14" viewBox="0 0 16 14"><rect x="1" y="2" width="14" height="10" fill="none" stroke="#333" stroke-width="1.4"/><path d="M1 2 L8 8 L15 2" fill="none" stroke="#333" stroke-width="1.4"/></svg><span>info@companyname.com</span></div>
  </div>
  <div class="abs foot-col" style="left:425px"><h4>COMPANY</h4><ul><li>Home</li><li>About us</li><li>Services</li><li>Products</li><li>Contact</li></ul></div>
  <div class="abs foot-col" style="left:570px"><h4>PRODUCTS</h4><ul><li>Sed porta</li><li>Suspendisse quam</li><li>Leo molestie</li><li>Sed luctus</li><li>Fermentum</li></ul></div>
  <div class="abs foot-col" style="left:750px"><h4>RESOURCES</h4><ul><li>FAQ</li><li>Videos</li><li>News</li><li>Contact Us</li></ul></div>
  <div class="abs foot-col social" style="left:915px"><h4>GET IN TOUCH</h4><ul><li><span class="dot"></span>Pulsefeed</li><li><span class="dot"></span>Circlepage</li><li><span class="dot"></span>Workwire</li><li><span class="dot"></span>Snapframe</li></ul></div>
</footer>
<div class="abs copyright" style="left:0;width:1200px">Copyright © 2019 All right reserved</div>

</body>
</html>
```